K & R Acre Works. Business card design

We need a business card designed for a new business. We have a bulldozer and tractor service. We clear land and make wildlife food plots. We provide disking, bush hogging, and site prep services.
I have attached an image of a business card that I like and would like my business cards to look similar.

Target Market(s)

anyone needing bulldozer and/or tractor services

Industry/Entity Type

Business

Contact Information for Business Card

K & R Acre Works, Operated by 7-T-Ranch
Wade Colton
601-472-3358
wcr4817@fieldmail-example.com

Font styles to use
Sans Serif

Colors

Designer to choose colors to be used in the design.

Requirements
Must have
• image of tractor and bulldozer
• Land Clearing
• Wildlife food plots
• Bush Hogging
• Disking
• Site prep
Nice to have
• i have included a image of a business card that i like. I would like mine to be similar.

```html
<!DOCTYPE html>
<html lang="en">
<head>
<meta charset="utf-8">
<title>K &amp; R Acre Works – Business Card</title>
<link href="https://fonts.googleapis.com/css2?family=Roboto:wght@400;500&family=Roboto+Condensed:wght@500;700&display=swap" rel="stylesheet">
<style>
  :root {
    --backdrop: #2b2b2b;
    --card-light: #f7f7f7;
    --card-shade: #e9e9e9;
    --brand-brown: #6e3f12;
    --band-brown: #7a4514;
    --olive: #8c8a2a;
    --ink-dark: #2a2a2a;
    --ink-body: #4a4a4a;
    --dot: #9aa033;
  }
  html, body {
    margin: 0;
    width: 1200px;
    height: 960px;
    overflow: hidden;
    background: var(--backdrop);
  }
  .canvas {
    position: relative;
    width: 1200px;
    height: 960px;
  }
  .card {
    position: absolute;
    left: 300px;
    top: 310px;
    width: 600px;
    height: 342px;
    border-radius: 22px;
    overflow: hidden;
    background: linear-gradient(180deg, var(--card-light), var(--card-shade));
    box-shadow: 0 4px 10px rgba(0,0,0,.45);
  }
  .card-art {
    position: absolute;
    inset: 0;
    width: 600px;
    height: 342px;
  }
  .brand {
    position: absolute;
    left: 28px;
    top: 64px;
    display: flex;
    align-items: center;
    gap: 6px;
  }
  .brand-mark {
    width: 14px;
    height: 14px;
    background: var(--olive);
  }
  .brand-name {
    font-family: "Roboto Condensed", sans-serif;
    font-weight: 700;
    font-size: 20px;
    letter-spacing: .3px;
    color: var(--brand-brown);
    text-transform: uppercase;
  }
  .tagline {
    position: absolute;
    left: 28px;
    top: 89px;
    font-family: "Roboto Condensed", sans-serif;
    font-weight: 700;
    font-size: 9.5px;
    color: var(--ink-dark);
    text-transform: uppercase;
  }
  .person-name {
    position: absolute;
    left: 27px;
    top: 118px;
    font-family: "Roboto Condensed", sans-serif;
    font-weight: 700;
    font-size: 21px;
    color: var(--olive);
    text-transform: uppercase;
  }
  .person-role {
    position: absolute;
    left: 27px;
    top: 142px;
    font-family: "Roboto Condensed", sans-serif;
    font-weight: 500;
    font-size: 15px;
    color: var(--brand-brown);
    text-transform: uppercase;
  }
  .contact, .services {
    position: absolute;
    left: 27px;
    margin: 0;
    padding: 0;
    list-style: none;
    font-family: "Roboto", sans-serif;
    font-size: 14px;
    line-height: 18px;
    color: var(--ink-body);
  }
  .contact { top: 168px; }
  .services { top: 226px; }
  .dot {
    display: inline-block;
    width: 5px;
    height: 5px;
    border-radius: 50%;
    background: var(--dot);
    margin: 0 4px 2px 5px;
    vertical-align: middle;
  }
</style>
</head>
<body>
<main class="canvas">
  <section class="card" aria-label="K &amp; R Acre Works business card">
    <svg class="card-art" viewBox="0 0 600 342" aria-hidden="false">
      <defs>
        <linearGradient id="scene-tone" x1="0" y1="0" x2="1" y2="1">
          <stop offset="0" stop-color="#4f6a3a"/>
          <stop offset=".45" stop-color="#6f7d3e"/>
          <stop offset=".7" stop-color="#c9b84a"/>
          <stop offset="1" stop-color="#8f8a66"/>
        </linearGradient>
        <linearGradient id="scene-fade" x1="0" y1="0" x2="0" y2="1">
          <stop offset=".65" stop-color="#f4f4f4" stop-opacity="0"/>
          <stop offset="1" stop-color="#f4f4f4" stop-opacity=".95"/>
        </linearGradient>
      </defs>
      <g role="img" aria-label="Photo of a yellow bulldozer and an orange tractor clearing brush on a wooded lot">
        <path d="M308,0 C290,80 285,140 300,200 C310,260 305,300 295,342 L600,342 L600,0 Z" fill="url(#scene-tone)"/>
        <path d="M308,0 C290,80 285,140 300,200 C310,260 305,300 295,342 L600,342 L600,0 Z" fill="url(#scene-fade)"/>
      </g>
      <path class="curve-band" d="M300,0 C275,60 265,120 285,190 C300,250 290,300 265,342 L295,342 C305,300 310,260 300,200 C285,140 290,80 308,0 Z" fill="var(--band-brown)"/>
    </svg>

    <div class="brand">
      <span class="brand-mark"></span>
      <span class="brand-name">K &amp; R Acre Works</span>
    </div>
    <div class="tagline">For all of your land improvement needs</div>

    <div class="person-name">Wade Colton</div>
    <div class="person-role">Owner</div>

    <ul class="contact">
      <li>P : 601-472-3358</li>
      <li>E : wcr4817@fieldmail-example.com</li>
      <li>www.kracreworks-example.com</li>
    </ul>

    <ul class="services">
      <li>Land Clearing</li>
      <li>Wildlife food plots</li>
      <li>Bush Hogging<span class="dot"></span>Disking<span class="dot"></span>Site prep</li>
    </ul>
  </section>
</main>
</body>
</html>
```